Bottle label design for 4 litre jug

Need to create a label for my chemical products please attached label. Must have the side labels, colors must be complimented with logo attached. Come up with a clean yet high end product look to it. the brand name is Varnon Glass cleaner, Trelby Shine Works is the logo,
Redisgn with new updated look, there are a total of 8 labels to be made for oterh products.

Industry/Entity Type

Cleaning industry

Font styles to use
Serif
Other font styles liked:
• Lora Bold, EB garamond, or use any font you choose, clean and bold

Colors
0054AA
0677BA
7BADD7
CADEEF
E8F1F8
0094D4
00A9DD
6FCCEA
C7EBF8
E9F6FB
00AB8E
00BBA5
67D7C9
C6EFE9
E9F9F6

```html
<!DOCTYPE html>
<html lang="en">
<head>
<meta charset="utf-8">
<title>Varnon Glass Cleaner – Jug Label</title>
<link href="https://fonts.googleapis.com/css2?family=Bebas+Neue&family=Montserrat:ital,wght@0,400;0,500;0,600;0,700;1,400;1,500;1,600;1,700&family=Lora:wght@700&display=swap" rel="stylesheet">
<style>
  :root{
    --page-bg:#c9c9c9;
    --label-bg:#dbe9ec;
    --info-panel:#eaf4f6;
    --teal:#00ab8e;
    --teal-light:#14b396;
    --blue-deep:#0054aa;
    --blue-mid:#0677ba;
    --ink:#1a1a1a;
    --white:#ffffff;
    --logo-box:#2a2a2a;
    --badge:#1db793;
  }
  *{margin:0;padding:0;box-sizing:border-box}
  html,body{width:1200px;height:960px;overflow:hidden}
  body{background:var(--page-bg);font-family:"Montserrat",sans-serif;color:var(--ink);position:relative}

  .label{position:absolute;left:30px;top:192px;width:1140px;height:577px;background:var(--label-bg);overflow:hidden}

  .front-panel{position:absolute;left:25px;top:18px;width:544px;height:545px;border-radius:38px;
    background:linear-gradient(170deg,#10a98e 0%,#0f9e92 35%,#0e85a6 70%,#0b5ea8 100%);overflow:hidden}
  .front-panel .sheen{position:absolute;inset:0}

  .brand-box{position:absolute;left:59px;top:0;width:197px;height:135px;background:var(--logo-box);
    border-radius:0 0 14px 14px;display:flex;align-items:center;justify-content:center;gap:10px;z-index:2}
  .brand-mark{width:14px;height:14px;background:var(--white)}
  .brand-name{color:var(--white);font-weight:500;font-size:14px;line-height:1.05;text-transform:uppercase;letter-spacing:.3px}

  .product-title{position:absolute;left:61px;top:142px;font-family:"Bebas Neue",sans-serif;font-size:94px;line-height:.86;color:var(--white);letter-spacing:.5px}
  .product-title .accent{color:var(--blue-deep)}

  .claim-en{position:absolute;left:62px;top:322px;width:440px;color:var(--white);font-weight:500;font-size:16px;line-height:1.3}
  .claim-fr{position:absolute;left:61px;top:374px;width:360px;color:var(--white);font-style:italic;font-size:14px;line-height:1.3}
  .rule{position:absolute;left:64px;top:423px;width:170px;height:1.5px;background:rgba(255,255,255,.85)}

  .features{position:absolute;left:62px;top:442px;display:flex;align-items:flex-start}
  .feature{display:flex;flex-direction:column;align-items:center;padding:0 12px}
  .feature:first-child{padding-left:0}
  .feature + .feature{border-left:1px solid rgba(255,255,255,.75)}
  .feature-pill{background:var(--badge);color:var(--white);font-family:"Lora",serif;font-weight:700;font-size:14.5px;padding:2px 8px;border-radius:3px;white-space:nowrap}
  .feature-fr{color:var(--white);font-style:italic;font-size:12.5px;margin-top:7px;white-space:nowrap}

  .footer-row{position:absolute;left:64px;top:507px;right:28px;display:flex;align-items:center}
  .qms{display:flex;align-items:center;gap:8px;color:var(--white);font-weight:600;font-size:11.5px;line-height:1.15}
  .sizes{display:flex;gap:11px;margin-left:22px}
  .size{border:1.5px solid var(--white);color:var(--white);border-radius:5px;font-size:9.5px;font-weight:600;padding:3px 7px}
  .certs{margin-left:auto;display:flex;gap:14px;align-items:center}
  .cert-badge{background:rgba(20,40,60,.55)}
  .cert-a{width:62px;height:24px;border-radius:4px}
  .cert-b{width:34px;height:34px;border-radius:50%}

  .info-panel{position:absolute;left:560px;top:18px;width:348px;height:545px;background:var(--info-panel);border-radius:0 38px 38px 0}
  .directions{position:absolute;left:591px;top:40px;width:240px;font-size:15.2px;line-height:1.33}
  .directions p{margin-bottom:9px}
  .directions .strong{font-weight:600}
  .directions .fr{font-style:italic}
  .directions .gap{margin-top:24px}

  .safety{position:absolute;left:876px;top:28px;width:250px;font-size:8.6px;line-height:1.25;color:var(--ink)}
  .safety p{margin-bottom:6px}
  .safety b{font-weight:700}
  .safety .fr{font-style:italic}
  .hazard{display:flex;gap:8px;align-items:flex-start;margin-bottom:6px}
  .hazard svg{flex:none}
  .company{font-style:italic;font-weight:700;font-size:11.5px;line-height:1.35;margin-top:8px}
</style>
</head>
<body>
<main class="label" aria-label="Varnon Glass Cleaner jug label">

  <section class="front-panel">
    <svg class="sheen" width="544" height="545" role="img" aria-label="Soft flowing teal and blue texture">
      <defs>
        <linearGradient id="glow" x1="0" y1="0" x2="1" y2="1">
          <stop offset="0" stop-color="#67d7c9" stop-opacity=".25"/>
          <stop offset="1" stop-color="#0054aa" stop-opacity=".15"/>
        </linearGradient>
      </defs>
      <rect width="544" height="545" fill="url(#glow)"/>
    </svg>
  </section>

  <div class="brand-box">
    <span class="brand-mark"></span>
    <span class="brand-name">Trelby<br>Shine<br>Works</span>
  </div>

  <h1 class="product-title"><span class="accent">Varnon</span> Glass<br>Cleaner</h1>

  <p class="claim-en">Dries fast without leaving a film or streaking.<br>Polishes as it dissolves dirt and dingy film.</p>
  <p class="claim-fr">Sans laisser de pellicules nide trainées. Dissout saleté et pellicule terne et fait briller.</p>
  <div class="rule"></div>

  <div class="features">
    <div class="feature"><span class="feature-pill">Biodegradeable</span><span class="feature-fr">Biodégradeatble</span></div>
    <div class="feature"><span class="feature-pill">Low Carbon Footprint</span><span class="feature-fr">Faible Empreinte Ecologiuqe</span></div>
    <div class="feature"><span class="feature-pill">Non Corrosive</span><span class="feature-fr">Non-Corrosif</span></div>
  </div>

  <div class="footer-row">
    <div class="qms">
      <svg width="26" height="26" viewBox="0 0 26 26" aria-hidden="true">
        <rect x="2" y="4" width="20" height="20" rx="4" fill="none" stroke="#fff" stroke-width="2"/>
        <path d="M7 13l5 6 12-16" fill="none" stroke="#fff" stroke-width="2.4" stroke-linecap="round" stroke-linejoin="round"/>
      </svg>
      <span>Compliant QMS<br>Mfg. Process</span>
    </div>
    <div class="sizes"><span class="size">4L</span><span class="size">20L</span><span class="size">205L</span></div>
    <div class="certs">
      <span class="cert-badge cert-a" role="img" aria-label="Eco certification badge"></span>
      <span class="cert-badge cert-b" role="img" aria-label="Green certification badge"></span>
    </div>
  </div>

  <section class="info-panel"></section>

  <section class="directions">
    <p>Read entire label before using. For industrial and institutional use only.</p>
    <p class="strong">Keep out of reach of children.</p>
    <p>For windows, glass, mirrors, windshields, ceramic tile, porcelain, etc. Use full strength. Spray on and wipe off with a clean towel or cloth.</p>
    <p class="strong">NOT AFFECTED BY FREEZING.</p>
    <p class="fr gap">Lire l’étiquette au complet avant d’utiliser le produit. Pour usage industriel ou dans un établissement seulement.</p>
    <p class="fr strong">Garder hors de la portée des enfants.</p>
    <p class="fr">Pour vitres, miroirs, carreaux en céramique, verre, porcelaine, etc. Ne pas diluer. Vaporiser et essuyer à l’aide d’un chiffon propre.</p>
    <p class="fr strong">NE CRAINT PAS LE GEL.</p>
  </section>

  <section class="safety">
    <p><b>WARNING:</b> Causes eye irritation. Prolonged or repeated skin contact may cause irritation.</p>
    <p><b>PRECAUTIONS:</b> Wash hands thoroughly after handling. Wear protective gloves/eye protection /face protection. Do not eat, drink or smoke when using this product.</p>
    <p><b>FIRST AID:</b><br><b>IF IN EYES:</b> Rinse cautiously with water for several minutes. Remove contact lenses, if present and easy to do. Continue rinsing. If eye irritation persists: get medical attention/advice.</p>
    <p><b>IF SWALLOWED:</b> Rinse mouth. <b>Do NOT</b> induce vomiting. Drink large quantities of water. Call a <b>POISON CENTER</b> or doctor/physician if you feel unwell. If skin irritation occurs: Get medical advice /attention.</p>
    <p><b>See Safety Data Sheet.</b></p>
    <div class="hazard">
      <svg width="62" height="44" viewBox="0 0 62 44" aria-hidden="true">
        <path d="M31 2 L60 22 L31 42 L2 22 Z" fill="#fff" stroke="#d4202a" stroke-width="3" stroke-linejoin="round" transform="translate(0,0)"/>
        <rect x="29" y="11" width="4" height="15" rx="1.5" fill="#111"/>
        <circle cx="31" cy="31" r="2.5" fill="#111"/>
      </svg>
      <p class="fr"><b>ATTENTION: Provoque une irritation oculaire. Un contact cutané prolongé ou répété peut provoquer une irritation.</b></p>
    </div>
    <p class="fr"><b>PRÉCAUTIONS:</b> Se laver soigneusement après la manipulation. Porter des gants de protection/ protection des yeux/protection du visage. Ne pas manger, boire ou fumer lors de l’utilisation de ce produit.</p>
    <p class="fr"><b>PREMIERS SOINS:</b></p>
    <p class="fr"><b>EN CAS DE CONTACT AVEC LES YEUX:</b> Rincer avec précaution à l’eau pendant plusieurs minutes. Enlever les lentilles de contact si la victime en porte. Continuer à rincer. Si l’irritation persiste: consulter un médecin. <b>EN CAS D’INGESTION:</b> Rincer la bouche. NE PAS faire vomir. Boire de grandes quantités d’eau. Appeler le CENTRE ANTIPOISON/ un médecin en cas de malaise.</p>
    <p class="fr">Consulter la fiche de données de sécurité.</p>
    <p class="company">TRELBY SHINE WORKS<br>Brantmoor, Ontario K9R 2T4</p>
  </section>

</main>
</body>
</html>
```